Mayhon online ordering platform looking for a great web design

Mayhon - from the Vietnamese words Mây Hồng meaning financial success.
Background
Mayhon is an online ordering platform for small retail businesses (corner stores). The idea is that small retailers will use the website to order their supplies. From this we will utilise the group buying to get better deals for them that they could not achieve individually.
We are looking for a simple but stylish design for our ordering page. The layout needs to be efficient, logical and self explanatory.
Products to be sold on the site are FMCG (fast moving consumer goods). Potential to be 000's of items.
Considerations
- end users are not technologically adept.
- Users are generally older so small print will not be well received.
- Use of touch screen monitors to select/change items so spacing in design is vital.
- Logical display of category and sub-categories.
- Easy selection of products to order as well as modification of quantity.
- Shopping cart with easy change of item quantity.
- List of items for ordering can be paginated.
- Items listed will have image for easy identification.
- Search box
- Format should be in psd (photoshop) or complete html/css
- All this information needs to be displayed on the one page.
Product information to contain the following:
- Image
- Price
- Product name
- Size
Area for prominent display of specials without crowding the product information.

```html
<!DOCTYPE html>
<html lang="en">
<head>
<meta charset="utf-8">
<title>Mayhon – Sub Category</title>
<link href="https://fonts.googleapis.com/css2?family=Ubuntu:wght@400;500;700&family=Bebas+Neue&display=swap" rel="stylesheet">
<style>
:root{
  --accent:#f25c3b;
  --accent-dark:#e0432a;
  --text:#444;
  --muted:#666;
  --rule:#dcdcdc;
  --frame:#d6d6d6;
  --nav-top:#f6f2e6;
  --nav-bottom:#e6dfc9;
  --teal:#0bb9c5;
  --white:#fff;
}
*{box-sizing:border-box;margin:0;padding:0}
html,body{width:1200px;height:756px;overflow:hidden;background:var(--white)}
body{position:relative;font-family:"Ubuntu",sans-serif;color:var(--text)}
.abs{position:absolute}

/* promo banner */
.promo{left:130px;top:-2px;width:940px;height:171px;border:1px solid var(--frame);background:var(--white)}
.promo-art{left:6px;top:0;width:926px;height:163px;background:var(--teal);overflow:hidden}
.promo-model{left:0;top:0;width:300px;height:163px;background:linear-gradient(90deg,#e9e6e2 0%,#f1efec 45%,#d9d3cf 70%,var(--teal) 100%)}
.promo-upto{left:300px;top:52px;font-family:"Bebas Neue",sans-serif;font-size:40px;color:var(--white);transform:rotate(-90deg);transform-origin:left top;line-height:1;top:122px}
.promo-deal{left:372px;top:4px;font-family:"Bebas Neue",sans-serif;font-size:150px;line-height:1;color:var(--white);letter-spacing:2px}
.promo-btn{left:835px;top:128px;width:91px;height:28px;background:#f1ede4;border:1px solid #cfc8b8;font-size:13px;color:#555;display:flex;align-items:center;justify-content:center}

/* category navigation */
.nav{left:129px;top:177px;width:941px;height:34px;border:1px solid #d8d2bf;background:linear-gradient(var(--nav-top),var(--nav-bottom))}
.nav-item{top:0;height:32px;border-right:1px solid #cfc7b0;font-size:14px;color:#555;padding-left:14px;display:flex;align-items:center}
.nav-item .caret{position:absolute;right:9px;top:14px;width:0;height:0;border-left:3px solid transparent;border-right:3px solid transparent;border-top:4px solid #777}
.nav-item.is-open{background:var(--accent);color:var(--white);font-weight:500;border:1px solid var(--accent-dark);top:-1px;height:34px}
.nav-item.is-open .caret{border-top-color:var(--white)}
.search{left:723px;top:3px;width:213px;height:26px;background:var(--white);border:1px solid #d5cfbe;font-size:12px;font-style:italic;color:#666;padding-left:10px;display:flex;align-items:center}

/* dropdown menus */
.menu{background:var(--white);border:1px solid #cfcfcf;border-top:none}
.menu-item{position:absolute;left:6px;right:4px;font-size:13px;color:#444;border-bottom:1px solid #d9d9d9;display:flex;align-items:center;padding-left:0}
.menu-item.is-hover{left:-1px;right:-1px;background:linear-gradient(#f7673f,#ee4f2d);color:var(--white);font-weight:500;border:1px solid var(--accent-dark);padding-left:7px}
.menu-item.last{border-bottom:none}

/* heading */
.crumbs{left:130px;top:224px;font-size:11px;color:#444}
.crumbs .current{color:var(--accent)}
.page-title{left:130px;top:240px;font-size:26px;font-weight:700;color:var(--accent)}

/* product panels */
.panel{left:129px;width:940px;border:1px solid var(--frame);background:var(--white)}
.panel-title{left:10px;top:9px;font-size:18px;color:var(--accent)}
.panel-title small{font-size:12px;color:#555}
.panel-rule{left:10px;width:913px;height:1px;background:var(--rule)}
.col-sep{width:1px;background:var(--rule)}
.product-shot{border-radius:18px 18px 8px 8px}
.product-name{font-size:12px;font-weight:500;color:var(--accent)}
.product-meta{font-size:12px;color:#444;width:132px;display:flex;justify-content:space-between}
</style>
</head>
<body>

<section class="promo abs">
  <div class="promo-art abs">
    <div class="promo-model abs" role="img" aria-label="Photo of a smiling shopper in a white top and red scarf"></div>
    <div class="promo-upto abs">UPTO</div>
    <div class="promo-deal abs">20% OFF</div>
    <div class="promo-btn abs">Learn More</div>
  </div>
</section>

<nav class="nav abs">
  <div class="nav-item abs" style="left:0;width:179px">Main Category<span class="caret"></span></div>
  <div class="nav-item abs" style="left:179px;width:178px">Sub Category<span class="caret"></span></div>
  <div class="nav-item abs is-open" style="left:357px;width:180px">Optional Category<span class="caret"></span></div>
  <div class="search abs">search category</div>
</nav>

<div class="crumbs abs">Home &gt; Main Category &gt; <span class="current">Sub Category</span></div>
<h1 class="page-title abs">Sub Category</h1>

<section class="panel abs" style="top:284px;height:285px">
  <h2 class="panel-title abs" style="font-weight:400">Featured Products</h2>
  <div class="panel-rule abs" style="top:39px"></div>
  <div class="col-sep abs" style="left:179px;top:52px;height:198px"></div>
  <div class="col-sep abs" style="left:366px;top:52px;height:198px"></div>
  <div class="col-sep abs" style="left:553px;top:52px;height:198px"></div>
  <div class="col-sep abs" style="left:740px;top:52px;height:198px"></div>

  <div class="product-shot abs" style="left:65px;top:54px;width:62px;height:170px;background:linear-gradient(90deg,#2f9e1c,#6fdc2e,#2f9e1c)" role="img" aria-label="Green shampoo bottle"></div>
  <div class="product-shot abs" style="left:248px;top:66px;width:60px;height:158px;background:linear-gradient(90deg,#dfe6f2,#ffffff,#1d3f9a)" role="img" aria-label="White and blue shampoo bottle"></div>
  <div class="product-shot abs" style="left:437px;top:150px;width:70px;height:74px;background:linear-gradient(90deg,#e6e6e6,#ffffff,#dadada)" role="img" aria-label="White shampoo bottle"></div>
  <div class="product-shot abs" style="left:808px;top:62px;width:56px;height:160px;background:linear-gradient(90deg,#b8103e,#f0467a,#b8103e)" role="img" aria-label="Pink shampoo bottle"></div>

  <div class="product-name abs" style="left:28px;top:230px">Product Name</div>
  <div class="product-meta abs" style="left:28px;top:248px"><span>500ml</span><span>$2.59</span></div>
  <div class="product-name abs" style="left:205px;top:230px">Product Name</div>
  <div class="product-meta abs" style="left:205px;top:248px"><span>500ml</span><span>$2.59</span></div>
  <div class="product-name abs" style="left:392px;top:230px">Product Name</div>
  <div class="product-meta abs" style="left:392px;top:248px"><span>500ml</span><span>$2.59</span></div>
  <div class="product-meta abs" style="left:690px;top:248px;width:30px;justify-content:flex-end"><span>9</span></div>
  <div class="product-name abs" style="left:772px;top:230px">Product Name</div>
  <div class="product-meta abs" style="left:772px;top:248px"><span>500ml</span><span>$2.59</span></div>
</section>

<section class="panel abs" style="top:575px;height:200px">
  <h2 class="panel-title abs" style="font-weight:400">Latest Arrivals <small>(see all)</small></h2>
  <div class="panel-rule abs" style="top:39px"></div>
  <div class="col-sep abs" style="left:179px;top:52px;height:150px"></div>
  <div class="col-sep abs" style="left:366px;top:52px;height:150px"></div>
  <div class="col-sep abs" style="left:553px;top:52px;height:150px"></div>
  <div class="col-sep abs" style="left:740px;top:52px;height:150px"></div>
  <div class="product-shot abs" style="left:65px;top:54px;width:62px;height:140px;background:linear-gradient(90deg,#2f9e1c,#6fdc2e,#2f9e1c)" role="img" aria-label="Green shampoo bottle"></div>
  <div class="product-shot abs" style="left:248px;top:66px;width:60px;height:130px;background:linear-gradient(90deg,#dfe6f2,#ffffff,#1d3f9a)" role="img" aria-label="White and blue shampoo bottle"></div>
  <div class="product-shot abs" style="left:438px;top:62px;width:68px;height:130px;background:linear-gradient(90deg,#e4e4e4,#ffffff,#d5d5d5)" role="img" aria-label="White shampoo bottle"></div>
  <div class="product-shot abs" style="left:625px;top:62px;width:68px;height:130px;background:linear-gradient(90deg,#e4e4e4,#ffffff,#d5d5d5)" role="img" aria-label="White shampoo bottle"></div>
  <div class="product-shot abs" style="left:808px;top:62px;width:56px;height:130px;background:linear-gradient(90deg,#b8103e,#f0467a,#b8103e)" role="img" aria-label="Pink shampoo bottle"></div>
</section>

<div class="menu abs" style="left:487px;top:210px;width:180px;height:222px">
  <div class="menu-item" style="top:0;height:33px">Drop Down</div>
  <div class="menu-item" style="top:33px;height:38px">Example</div>
  <div class="menu-item" style="top:71px;height:38px">shown here</div>
  <div class="menu-item" style="top:109px;height:38px">and</div>
  <div class="menu-item is-hover" style="top:146px;height:39px">Category Hover</div>
  <div class="menu-item last" style="top:185px;height:36px">Example</div>
</div>

<div class="menu abs" style="left:667px;top:356px;width:181px;height:220px;border-top:1px solid #cfcfcf">
  <div class="menu-item" style="top:0;height:31px">Drop Down</div>
  <div class="menu-item" style="top:31px;height:38px">Example</div>
  <div class="menu-item" style="top:69px;height:38px">shown here</div>
  <div class="menu-item" style="top:107px;height:38px">and</div>
  <div class="menu-item" style="top:145px;height:38px">Fifth brand</div>
  <div class="menu-item last" style="top:183px;height:36px">Example</div>
</div>

<svg class="abs" style="left:561px;top:370px" width="20" height="26" viewBox="0 0 20 26" aria-hidden="true">
  <path d="M6 2.5c1 0 1.7.7 1.7 1.7V12l.2-1.6c.3-1.4 2.6-1.3 2.8.2l.1 1c.3-1.3 2.4-1.2 2.6.3l.1.9c.4-1.1 2.4-.9 2.5.6V19c0 2.8-2 5-4.8 5H9.5c-1.7 0-3.1-.9-3.9-2.3L2.4 16c-.7-1.2.9-2.5 2-1.4l.9 1V4.2C5.3 3.2 5.1 2.5 6 2.5z" fill="#fff" stroke="#111" stroke-width="1.1" stroke-linejoin="round"/>
</svg>

</body>
</html>
```